Onboarding Infographic/brochure

We are a small criminal defense firm looking to create some sort of infographic or brochure that we can onboard new clients with. We are currently sending it out via email but want something a bit cooler and fun to send to clients. The information is:

A Few Quick Rules

We are here to help each step of the way. While questions are never discouraged, this letter will answer some of the most common ones we get asked.

Communications

As a client, you should always be in the loop. While we will try to respond to questions as quickly as possible, sometimes we are unable to respond right away. Do not worry - we promise to get back to you soon. Some questions might take some time to research, and a correct answer is better than a quick one.

Appointments

One of the benefits of having an attorney is the ability to discuss your case outside of court, minus the stress and headaches. If you need an appointment, please contact the office.

Appointments must be scheduled in advance. We do not want you to make a special trip to the office only to learn that we are in court or otherwise unavailable.

Jail Visits

If your family member is currently in jail, we take that very seriously. We will visit your loved one and introduce ourselves. While the case is ongoing, we ask that a family member be designated a “contact” person so that messages can be relayed quickly. Never discuss the facts of the case over the phone with someone who is in jail. Jail calls are recorded and we have seen too many cases go south based on remarks made over recorded lines.

Police Reports and Discovery

We will do our best to provide you with copies of everything we receive on your case. Most information will be emailed, so please keep your email address up to date.

Changes in Contact Information

If you move or change numbers during the case, please let us know. It is difficult to help if we are unable to reach you, and helping you is why we are here.

Court Appearances

Cases do not get resolved as quickly as they do on television. Expect there to be several hearings in your case and it may be necessary for you to attend one or more of them. If a hearing is set, you will receive notice of the date and time of each hearing.

Billing and Collections

We understand that this investment was a huge decision for you. As we focus on providing the best representation, we will need for you to stay on schedule with any payment arrangements agreed to at the time of your initial consultation.

Again, thank you for your trust in us. We look forward to getting a fantastic outcome on your case.

Target Market(s)

Criminal defense clients and their families

Industry/Entity Type

Legal

Font styles to use
Serif

Requirements
Must have
• Must incorporate all of the rules we email out. Would like diagrams, images or pictures
Nice to have
• We attached a Welcome brochure. Not sure I want it to look super similar, hence the request for infographic.

```html
<!DOCTYPE html>
<html lang="en">
<head>
<meta charset="utf-8">
<title>Meridian Legal Group – A Few Quick Rules</title>
<link rel="stylesheet" href="https://fonts.googleapis.com/css2?family=Roboto:ital,wght@0,400;0,500;1,400&family=Roboto+Slab:wght@700&display=swap">
<style>
:root{
  --navy:#0a45a6;
  --sky:#1597dc;
  --band-start:#0448aa;
  --band-end:#129ce0;
  --ink:#2b2b2b;
  --rule:#c7c7c7;
  --stripe:#eef0f3;
  --white:#ffffff;
}
*{margin:0;padding:0;box-sizing:border-box}
html,body{width:848px;height:1200px;overflow:hidden;background:var(--white)}
.sheet{position:relative;width:848px;height:1200px;overflow:hidden;font-family:"Roboto",Arial,sans-serif;color:var(--ink)}
.backdrop{position:absolute;inset:0}
.masthead{position:absolute;left:0;top:0;width:848px;height:121px;background:linear-gradient(90deg,var(--band-start),var(--band-end));display:flex;align-items:center;justify-content:center;gap:12px}
.masthead-mark{width:16px;height:16px;background:var(--white)}
.masthead-name{color:var(--white);font-family:"Roboto",Arial,sans-serif;font-weight:500;font-size:34px;letter-spacing:.5px}
.page-title{position:absolute;top:160px;left:0;width:100%;text-align:center;font-family:"Roboto Slab",Georgia,serif;font-weight:700;font-size:34px;color:var(--navy);letter-spacing:.3px}
.title-rule{position:absolute;top:205px;left:377px;width:94px;height:1px;background:var(--rule)}
.title-rule::after{content:"";position:absolute;left:27px;top:-1px;width:40px;height:3px;border-radius:2px;background:var(--sky)}
.intro{position:absolute;top:225px;left:130px;width:588px;text-align:center;font-style:italic;font-size:11.2px;line-height:19px;color:var(--ink)}
.timeline{position:absolute;left:423.5px;top:330px;width:1px;height:690px;background:#b9b9b9}
.stop{position:absolute;width:14px;height:14px;left:417px;border-radius:50%;background:var(--white);border:1.5px solid var(--sky)}
.stop::after{content:"";position:absolute;left:3.5px;top:3.5px;width:4px;height:4px;border-radius:50%;background:var(--navy)}
.stop.dark{border-color:var(--navy)}
.node{position:absolute;width:84px;height:76px;filter:drop-shadow(0 3px 5px rgba(0,0,0,.18))}
.node.left{left:324px}
.node.right{left:441px}
.rule-block{position:absolute;width:240px}
.rule-block.left{left:65px;text-align:right}
.rule-block.right{left:543px;width:232px;text-align:left}
.rule-heading{font-size:13.4px;font-weight:500;line-height:20.6px;letter-spacing:.2px;margin-bottom:2px}
.rule-block.left .rule-heading{color:var(--navy)}
.rule-block.right .rule-heading{color:var(--sky)}
.rule-text{font-size:10.6px;line-height:18.2px;color:var(--ink)}
.rule-text + .rule-text{margin-top:6px}
.closing{position:absolute;top:1150px;left:0;width:100%;text-align:center;font-style:italic;font-size:11.5px;color:var(--ink)}
</style>
</head>
<body>
<div class="sheet">
  <svg class="backdrop" width="848" height="1200" viewBox="0 0 848 1200" aria-hidden="true">
    <polygon points="520,121 848,121 848,420" fill="var(--stripe)" opacity=".6"/>
    <polygon points="430,560 848,980 848,1060 380,590" fill="var(--stripe)" opacity=".7"/>
    <polygon points="300,900 848,1120 848,1200 640,1200 260,940" fill="var(--stripe)" opacity=".5"/>
    <polygon points="0,240 120,121 190,121 0,310" fill="var(--stripe)" opacity=".5"/>
  </svg>

  <header class="masthead">
    <span class="masthead-mark"></span>
    <span class="masthead-name">MERIDIAN LEGAL GROUP</span>
  </header>

  <h1 class="page-title">A FEW QUICK RULES</h1>
  <div class="title-rule"></div>
  <p class="intro">We are here to help each step of the way. While questions are never discouraged, this letter will answer some of the most common ones we get asked.</p>

  <div class="timeline"></div>
  <span class="stop dark" style="top:323px"></span>
  <span class="stop" style="top:438px"></span>
  <span class="stop dark" style="top:553px"></span>
  <span class="stop" style="top:668px"></span>
  <span class="stop dark" style="top:783px"></span>
  <span class="stop" style="top:898px"></span>
  <span class="stop dark" style="top:1013px"></span>

  <!-- Communications -->
  <svg class="node left" style="top:292px" viewBox="0 0 84 76">
    <polygon points="70,32 79,38 70,44" fill="var(--navy)"/>
    <circle cx="38" cy="38" r="33" fill="var(--white)" stroke="var(--navy)" stroke-width="5"/>
    <g transform="translate(38 38)" fill="var(--navy)">
      <path d="M-2,-5 h12 a8,8 0 0 1 8,8 v4 a8,8 0 0 1 -4,7 l3,6 l-8,-4 h-11 a8,8 0 0 1 -8,-8 v-5 a8,8 0 0 1 8,-8z" stroke="var(--white)" stroke-width="2"/>
      <path d="M-10,-15 h14 a8,8 0 0 1 8,8 v4 a8,8 0 0 1 -8,8 h-10 l-8,5 l2,-6 a8,8 0 0 1 -6,-7 v-4 a8,8 0 0 1 8,-8z"/>
      <circle cx="-8" cy="-5" r="1.7" fill="var(--white)"/>
      <circle cx="-3" cy="-5" r="1.7" fill="var(--white)"/>
      <circle cx="2" cy="-5" r="1.7" fill="var(--white)"/>
    </g>
  </svg>
  <div class="rule-block left" style="top:289px">
    <h2 class="rule-heading">COMMUNICATIONS</h2>
    <p class="rule-text">As a client, you should always be in the loop. While we will try to respond to questions as quickly as possible, sometimes we are unable to respond right away. Do not worry - we promise to get back to you soon. Some questions might take some time to research, and a correct answer is better than a quick one.</p>
  </div>

  <!-- Appointments -->
  <svg class="node right" style="top:407px" viewBox="0 0 84 76">
    <polygon points="14,32 5,38 14,44" fill="var(--sky)"/>
    <circle cx="46" cy="38" r="33" fill="var(--white)" stroke="var(--sky)" stroke-width="5"/>
    <g transform="translate(46 38)" fill="var(--sky)">
      <rect x="-16" y="-13" width="25" height="27" rx="3"/>
      <rect x="-12" y="-17" width="3" height="6" rx="1.5"/>
      <rect x="2" y="-17" width="3" height="6" rx="1.5"/>
      <rect x="-12" y="-4" width="7" height="2.4" fill="var(--white)"/>
      <rect x="-12" y="2" width="10" height="2.4" fill="var(--white)"/>
      <circle cx="9" cy="4" r="5" stroke="var(--white)" stroke-width="2"/>
      <path d="M0,17 a9,8 0 0 1 18,0z" stroke="var(--white)" stroke-width="2"/>
    </g>
  </svg>
  <div class="rule-block right" style="top:404px">
    <h2 class="rule-heading">APPOINTMENTS</h2>
    <p class="rule-text">One of the benefits of having an attorney is the ability to discuss your case outside of court, minus the stress and headaches. If you need an appointment, please contact the office.</p>
    <p class="rule-text">Appointments must be scheduled in advance. We do not want you to make a special trip to the office only to learn that we are in court or otherwise unavailable.</p>
  </div>

  <!-- Jail visits -->
  <svg class="node left" style="top:522px" viewBox="0 0 84 76">
    <polygon points="70,32 79,38 70,44" fill="var(--navy)"/>
    <circle cx="38" cy="38" r="33" fill="var(--white)" stroke="var(--navy)" stroke-width="5"/>
    <g transform="translate(38 38)" fill="var(--navy)">
      <rect x="-1.2" y="-18" width="2.4" height="34"/>
      <circle cx="-10" cy="-2" r="3.5"/>
      <path d="M-16,12 v-5 a6,6 0 0 1 12,0 v5z"/>
      <circle cx="10" cy="-3" r="3.5"/>
      <rect x="4" y="3" width="12" height="1.8"/>
      <rect x="4" y="6.5" width="12" height="1.8"/>
      <rect x="4" y="10" width="12" height="1.8"/>
    </g>
  </svg>
  <div class="rule-block left" style="top:519px">
    <h2 class="rule-heading">JAIL VISITS</h2>
    <p class="rule-text">If your family member is currently in jail, we take that very seriously. We will visit your loved one and introduce ourselves. While the case is ongoing, we ask that a family member be designated a “contact” person so that messages can be relayed quickly. Never discuss the facts of the case over the phone with someone who is in jail. Jail calls are recorded and we have seen too many cases go south based on remarks made over recorded lines.</p>
  </div>

  <!-- Police reports -->
  <svg class="node right" style="top:637px" viewBox="0 0 84 76">
    <polygon points="14,32 5,38 14,44" fill="var(--sky)"/>
    <circle cx="46" cy="38" r="33" fill="var(--white)" stroke="var(--sky)" stroke-width="5"/>
    <g transform="translate(46 38)" fill="var(--sky)">
      <path d="M-16,-12 v28 h18 v-2 h-16 v-26z"/>
      <path d="M-12,-17 h14 l6,6 v23 h-20z"/>
      <rect x="-9" y="-9" width="11" height="2" fill="var(--white)"/>
      <rect x="-9" y="-4" width="11" height="2" fill="var(--white)"/>
      <rect x="-9" y="1" width="8" height="2" fill="var(--white)"/>
      <circle cx="9" cy="8" r="8" stroke="var(--white)" stroke-width="2"/>
      <polygon points="9,3.5 10.4,6.6 13.6,6.8 11.1,8.9 12,12 9,10.2 6,12 6.9,8.9 4.4,6.8 7.6,6.6" fill="var(--white)"/>
    </g>
  </svg>
  <div class="rule-block right" style="top:634px">
    <h2 class="rule-heading">POLICE REPORTS AND<br>DISCOVERY</h2>
    <p class="rule-text">We will do our best to provide you with copies of everything we receive on your case. Most information will be emailed, so please keep your email address up to date.</p>
  </div>

  <!-- Changes in contact information -->
  <svg class="node left" style="top:752px" viewBox="0 0 84 76">
    <polygon points="70,32 79,38 70,44" fill="var(--navy)"/>
    <circle cx="38" cy="38" r="33" fill="var(--white)" stroke="var(--navy)" stroke-width="5"/>
    <g transform="translate(38 38)" fill="var(--navy)">
      <path d="M-15,-8 l5,-4 l5,7 l-3,3 c2,5 5,8 10,10 l3,-3 l7,5 l-4,5 c-12,-1 -22,-11 -23,-23z"/>
      <path d="M0,-17 h13 a3,3 0 0 1 3,3 v8 a3,3 0 0 1 -3,3 h-7 l-4,3 v-3 h-2 a3,3 0 0 1 -3,-3 v-8 a3,3 0 0 1 3,-3z"/>
      <circle cx="3" cy="-10" r="1.3" fill="var(--white)"/>
      <circle cx="7" cy="-10" r="1.3" fill="var(--white)"/>
      <circle cx="11" cy="-10" r="1.3" fill="var(--white)"/>
    </g>
  </svg>
  <div class="rule-block left" style="top:749px">
    <h2 class="rule-heading">CHANGES IN CONTACT<br>INFORMATION</h2>
    <p class="rule-text">If you move or change numbers during the case, please let us know. It is difficult to help if we are unable to reach you, and helping you is why we are here.</p>
  </div>

  <!-- Court appearances -->
  <svg class="node right" style="top:867px" viewBox="0 0 84 76">
    <polygon points="14,32 5,38 14,44" fill="var(--sky)"/>
    <circle cx="46" cy="38" r="33" fill="var(--white)" stroke="var(--sky)" stroke-width="5"/>
    <g transform="translate(46 38)" fill="var(--sky)">
      <circle cx="-9" cy="-14" r="2.6"/><path d="M-14,-7 a5,5 0 0 1 10,0z"/>
      <circle cx="0" cy="-14" r="2.6"/><path d="M-5,-7 a5,5 0 0 1 10,0z"/>
      <circle cx="9" cy="-14" r="2.6"/><path d="M4,-7 a5,5 0 0 1 10,0z"/>
      <rect x="-17" y="-6" width="34" height="2.5"/>
      <rect x="-15" y="-3" width="30" height="7"/>
      <circle cx="-2" cy="8" r="3"/>
      <path d="M-7,17 a5,5 0 0 1 10,0z"/>
      <rect x="5" y="6" width="7" height="9" rx="1"/>
    </g>
  </svg>
  <div class="rule-block right" style="top:864px">
    <h2 class="rule-heading">COURT APPEARANCES</h2>
    <p class="rule-text">Cases do not get resolved as quickly as they do on television. Expect there to be several hearings in your case and it may be necessary for you to attend one or more of them. If a hearing is set, you will receive notice of the date and time of each hearing.</p>
  </div>

  <!-- Billing -->
  <svg class="node left" style="top:982px" viewBox="0 0 84 76">
    <polygon points="70,32 79,38 70,44" fill="var(--navy)"/>
    <circle cx="38" cy="38" r="33" fill="var(--white)" stroke="var(--navy)" stroke-width="5"/>
    <g transform="translate(38 38)" fill="var(--navy)">
      <path d="M-12,-13 h18 v27 a3,3 0 0 1 -3,3 h-19 a3,3 0 0 0 4,-3z"/>
      <rect x="-17" y="12" width="6" height="5" rx="1"/>
      <circle cx="-8" cy="-6" r="1.4" fill="var(--white)"/>
      <rect x="-5" y="-7" width="8" height="2" fill="var(--white)"/>
      <circle cx="-8" cy="0" r="1.4" fill="var(--white)"/>
      <rect x="-5" y="-1" width="8" height="2" fill="var(--white)"/>
      <circle cx="-8" cy="6" r="1.4" fill="var(--white)"/>
      <rect x="-5" y="5" width="8" height="2" fill="var(--white)"/>
      <circle cx="9" cy="-12" r="7.5" stroke="var(--white)" stroke-width="2"/>
      <text x="9" y="-8.5" text-anchor="middle" font-family="Roboto, Arial, sans-serif" font-size="10" font-weight="500" fill="var(--white)">$</text>
    </g>
  </svg>
  <div class="rule-block left" style="top:979px">
    <h2 class="rule-heading">BILLING AND COLLECTIONS</h2>
    <p class="rule-text">We understand that this investment was a huge decision for you. As we focus on providing the best representation, we will need for you to stay on schedule with any payment arrangements agreed to at the time of your initial consultation.</p>
  </div>

  <p class="closing">Again, thank you for your trust in us. We look forward to getting a fantastic outcome on your case.</p>
</div>
</body>
</html>
```